Modern Business Card for Larkwell 2018

Our company assumes the best about people. We are creating an online community of entrepreneurs and business leaders who struggle with marketing their business online.

This business card should POP! We recently got a new logo and are launching a new website next month, so our business cards should make a statement that feels:
-Fresh
-Smart
-Trustworthy
-Fun

Target Market(s)

small business owners, entrepreneurs

Industry/Entity Type

Digital Marketing

Contact Information for Business Card

Dimensions: 3.5" x 2"

Font styles to use
Sans Serif

Colors
f37122
ffffff

Requirements
Must have
• We need a business card with a modern, bold design. We will use one side of the card as a lead-generation offer, so text on one side will need to fit up to 140 characters. The business card should stick to our core colors (orange, black, and white).
Nice to have
• We think a vertical "portrait" design could be interesting.
Should not have
• Should not look like a traditional business card. The round icon should stand out from a distance.

```html
<!DOCTYPE html>
<html lang="en">
<head>
<meta charset="utf-8">
<title>Larkwell Business Card</title>
<link rel="stylesheet" href="https://fonts.googleapis.com/css2?family=Open+Sans:wght@400;600;700;800&display=swap">
<style>
  :root {
    --orange: #f37122;
    --card-orange: #e8621f;
    --white: #ffffff;
    --paper: #f4f4f4;
    --ink: #1e1e1e;
    --ink-soft: #444444;
    --backdrop: #2b2b2b;
    --rule: #333333;
  }
  * { margin: 0; padding: 0; box-sizing: border-box; }
  html, body {
    width: 1200px; height: 960px; overflow: hidden;
    background: var(--backdrop);
    font-family: "Open Sans", Arial, sans-serif;
  }
  .stage { position: relative; width: 1200px; height: 960px; }

  .card { position: absolute; width: 598px; height: 342px; overflow: hidden; }
  .card-front { left: 322px; top: 108px; background: var(--paper); }
  .card-back { left: 320px; top: 493px; background: var(--card-orange); }

  .brand-disc { position: absolute; left: 280px; top: 24px; width: 300px; height: 300px; }

  .contact { position: absolute; left: 27px; top: 258px; }
  .contact-name { color: var(--orange); font-weight: 700; font-size: 20px; letter-spacing: -0.2px; line-height: 24px; }
  .contact-role { color: var(--ink); font-weight: 700; font-size: 15px; line-height: 22px; margin-top: 4px; }
  .contact-email { color: var(--ink-soft); font-size: 15px; line-height: 20px; }

  .brand { position: absolute; left: 30px; top: 58px; width: 260px; text-align: center; color: var(--white); }
  .brand-dot { display: block; margin: 0 auto 6px; width: 40px; height: 40px; border-radius: 50%; background: var(--white); }
  .brand-name { font-weight: 700; font-size: 38px; line-height: 44px; letter-spacing: 0.5px; }
  .brand-tagline { font-weight: 700; font-size: 10px; letter-spacing: 0.6px; text-transform: uppercase; margin-top: 2px; }

  .divider { position: absolute; left: 297px; top: 27px; width: 1px; height: 164px; background: rgba(255,255,255,0.7); }

  .offer { position: absolute; left: 323px; top: 26px; width: 260px; color: var(--white); }
  .offer-headline { font-weight: 800; font-size: 20px; line-height: 22px; text-transform: uppercase; letter-spacing: 0.1px; }
  .offer-body { font-size: 14px; line-height: 20px; margin-top: 6px; }
  .offer-link { font-weight: 700; font-size: 18px; margin-top: 14px; }

  .notes { position: absolute; left: 20px; top: 217px; width: 557px; height: 101px; background: var(--paper); border-radius: 16px; }
  .notes-line { position: absolute; left: 24px; right: 27px; height: 1px; background: var(--rule); }
  .notes-line.first { top: 31px; }
  .notes-line.second { top: 71px; }
</style>
</head>
<body>
<main class="stage">
  <section class="card card-front">
    <svg class="brand-disc" viewBox="0 0 300 300" aria-hidden="true">
      <circle cx="150" cy="150" r="150" fill="var(--orange)"/>
    </svg>
    <div class="contact">
      <p class="contact-name">DANA WHITFIELD</p>
      <p class="contact-role">STORY MARKETING COACH</p>
      <p class="contact-email">dana@larkwellnow.com</p>
    </div>
  </section>

  <section class="card card-back">
    <div class="brand">
      <span class="brand-dot"></span>
      <p class="brand-name">LARKWELL</p>
      <p class="brand-tagline">Tell stories that inspire action</p>
    </div>
    <div class="divider"></div>
    <div class="offer">
      <p class="offer-headline">Reach more people.<br>Make more money.<br>Create more impact.</p>
      <p class="offer-body">Get your free Larkwell<br>Starter Package and our<br>marketing guide today at</p>
      <p class="offer-link">Larkwellnow.com/start</p>
    </div>
    <div class="notes">
      <div class="notes-line first"></div>
      <div class="notes-line second"></div>
    </div>
  </section>
</main>
</body>
</html>
```